Meridale Hair Studio Needs a new appointment business card

We need a new appointment card for our hair salon.

I Dont want bright out there colours.
I would like it to be neat, clean, easy to read. White, Black, with a hint of colour if needed.

We need
-Logo
-Phone number 47268315
-Mobile Number: 0437608251
Address: Shop 5/213 Tarwin Road, The Crossgate, Mackay 4740

BACK SIDE OF CARD
- Appointment Time & Date (White background so we are able to write on it)
(If you are unable to make your appointment please contact us ASAP 47268315)

I also would like the linkpage and Snapframe logo(Find us on Linkpage)(find us on Snapframe)

Target Market(s)

appointment card simple to read. all information for their next appoint For all our clients male and female

Industry/Entity Type

Hairdresser

Contact Information for Business Card

-Logo
-Phone number 47268315

BACK SIDE OF CARD

Font styles to use
Serif
Sans Serif
Script

Requirements
Must have
• White Back ground on backside with appointment deatils so we are able to write information (like appointment time and date)
Nice to have
• Find us on Linkpage
and
snapframe - meridale_hairstudio
Should not have
• BRIGHT COLOURS

```html
<!DOCTYPE html>
<html lang="en">
<head>
<meta charset="utf-8">
<title>Meridale Hair Studio – Appointment Card</title>
<link rel="stylesheet" href="https://fonts.googleapis.com/css2?family=Roboto+Slab:wght@300;400&family=Roboto:wght@400;700&display=swap">
<style>
  :root {
    --backdrop: #c8c9cb;
    --card-dark: #231f20;
    --card-light: #ffffff;
    --ink-white: #ffffff;
    --ink-dark: #333333;
    --rule: #555555;
    --decor-soft: #e6e7e8;
    --social-tone: #8a8c8f;
  }
  * { margin: 0; padding: 0; box-sizing: border-box; }
  html, body { width: 1200px; height: 1200px; overflow: hidden; }
  body { background: var(--backdrop); position: relative; font-family: "Roboto", Arial, sans-serif; }

  .card { position: absolute; width: 699px; height: 399px; border-radius: 18px; overflow: hidden; }

  /* Front */
  .card--front { left: 172px; top: 190px; background: var(--card-dark); color: var(--ink-white); }
  .contact { position: absolute; top: 27px; display: flex; align-items: center; gap: 12px; font-size: 20px; letter-spacing: 0.3px; }
  .contact--mobile { left: 55px; }
  .contact--phone { left: 508px; }
  .contact svg { display: block; }
  .brand-name { position: absolute; left: 0; right: 0; top: 150px; text-align: center; font-family: "Roboto Slab", Georgia, serif; font-weight: 400; font-size: 38px; letter-spacing: 3px; text-transform: uppercase; color: var(--ink-white); }
  .address { position: absolute; left: 0; right: 0; top: 299px; text-align: center; font-family: "Roboto Slab", Georgia, serif; font-weight: 300; font-size: 20px; letter-spacing: 0.2px; }

  /* Back */
  .card--back { left: 329px; top: 610px; background: var(--card-light); border: 1px solid var(--rule); color: var(--ink-dark); }
  .decor-area { position: absolute; right: 0; top: 0; width: 340px; height: 100%; background: linear-gradient(200deg, var(--decor-soft) 0%, rgba(230,231,232,0.35) 55%, rgba(255,255,255,0) 100%); }
  .appt-heading { position: absolute; left: 0; right: 0; top: 96px; text-align: center; font-family: "Roboto Slab", Georgia, serif; font-weight: 300; font-size: 25px; letter-spacing: 0.5px; }
  .field { position: absolute; left: 203px; display: flex; align-items: flex-end; font-weight: 700; font-size: 17px; letter-spacing: 0.5px; }
  .field--date { top: 189px; }
  .field--time { top: 252px; }
  .field__line { display: block; width: 155px; border-bottom: 1px solid var(--rule); margin-left: 22px; margin-bottom: 2px; }
  .field--time .field__line { margin-left: 24px; }
  .field__suffix { font-size: 11px; margin-left: 24px; margin-bottom: -2px; }
  .socials { position: absolute; left: 0; right: 0; top: 324px; display: flex; justify-content: center; gap: 28px; }
  .social { display: flex; align-items: center; gap: 8px; font-family: "Roboto Slab", Georgia, serif; font-weight: 400; font-size: 15px; color: var(--ink-dark); }
  .social__dot { width: 22px; height: 22px; border-radius: 50%; background: var(--social-tone); }
</style>
</head>
<body>
  <section class="card card--front" aria-label="Card front">
    <div class="contact contact--mobile">
      <svg width="16" height="26" viewBox="0 0 16 26" aria-hidden="true"><rect x="1.5" y="1.5" width="13" height="23" rx="2" fill="none" stroke="#fff" stroke-width="3"/></svg>
      <span>0437608251</span>
    </div>
    <div class="contact contact--phone">
      <svg width="20" height="24" viewBox="0 0 20 24" aria-hidden="true"><path d="M5 1 L9 6 L6.5 9 C7.5 12.5 10 15.5 13 17 L15.5 14.5 L19.5 19 L16 23 C8 21 2 12 2 4 Z" fill="#fff"/></svg>
      <span>47268315</span>
    </div>
    <h1 class="brand-name">Meridale Hair Studio</h1>
    <p class="address">Shop 5/213 Tarwin Road, The Crossgate, Mackay 4740</p>
  </section>

  <section class="card card--back" aria-label="Card back">
    <div class="decor-area" role="img" aria-label="Large faint scissors decoration"></div>
    <h2 class="appt-heading">YOUR NEXT APPOINTMENT IS</h2>
    <div class="field field--date"><span>DATE:</span><span class="field__line"></span></div>
    <div class="field field--time"><span>TIME:</span><span class="field__line"></span><span class="field__suffix">AM/PM</span></div>
    <div class="socials">
      <span class="social"><span class="social__dot"></span>Linkpage</span>
      <span class="social"><span class="social__dot"></span>Snapframe</span>
    </div>
  </section>
</body>
</html>
```